We need a new business card that reflects who we are. Professional, classy, modern, and service ori

We need a business card design for a window coverings design company in Kansas City called Bright Lane Interiors. We offer professional, modern, and high quality window covering products. We are looking to portray an image of a big, national franchise. We are a 5 location (with showrooms) business with 10 professional designers and 4 professional installers. These cards will be used with Thank you cards, given to realtors, and asked for referrals with.

Target Market(s)

Kansas City

Industry/Entity Type

Business

Contact Information for Business Card

We would like our card to look clean and simple on the front, featuring our logo and Marlow Fenwick's. Our designers' phone numbers and emails should be displayed as well as their title.

Font styles to use
Sans Serif

Colors

Designer to choose colors to be used in the design.

Requirements
Must have
• Front - Logos, name, phone number, email address
• Back - Showroom locations, social media? Appt date/time?
Nice to have
• I would like a clean and modern look (not contemporary. I like a white background, but I am open to ideas. Looking for a "National chain" look for a small business.
Should not have
• Too much busyness.

```html
<!DOCTYPE html>
<html lang="en">
<head>
<meta charset="utf-8">
<title>Bright Lane Interiors – Business Card</title>
<link rel="stylesheet" href="https://fonts.googleapis.com/css2?family=Arimo:wght@400;700&family=Tinos:wght@400;700&display=swap">
<style>
  :root {
    --backdrop: #2b2b2d;
    --card: #f7f7f7;
    --red: #c8383c;
    --ink: #2a2a2a;
    --grey: #707070;
    --rule: #9a9a9a;
    --dots: #b5b5b5;
  }
  * { box-sizing: border-box; margin: 0; padding: 0; }
  html, body { width: 1200px; height: 900px; overflow: hidden; }
  body { background: var(--backdrop); position: relative; font-family: "Arimo", Arial, sans-serif; }

  .card {
    position: absolute; width: 630px; height: 360px;
    background: var(--card);
    box-shadow: 0 10px 30px rgba(0,0,0,.45);
  }
  .card--back { left: 60px; top: 70px; }
  .card--front { left: 510px; top: 470px; }

  /* Back: appointment side */
  .brand { position: absolute; right: 40px; top: 34px; }
  .brand__name { display: flex; align-items: center; gap: 8px;
    font-family: "Tinos", serif; font-size: 26px; font-weight: 700; color: var(--red); }
  .brand__square { width: 18px; height: 18px; background: var(--red); }
  .brand__tagline { font-family: "Tinos", serif; font-size: 11px; color: var(--ink); margin-top: 3px; padding-left: 26px; }

  .partner { position: absolute; left: 34px; top: 130px; display: flex; align-items: center; gap: 8px;
    font-family: "Tinos", serif; font-size: 17px; font-weight: 700; color: var(--grey); }
  .partner__mark { width: 14px; height: 14px; border-radius: 50%; background: var(--grey); }

  .follow { position: absolute; right: 42px; top: 116px; text-align: center;
    font-size: 11px; font-weight: 700; color: var(--ink); letter-spacing: .5px; }
  .follow__icons { display: flex; gap: 4px; margin-top: 4px; justify-content: center; }
  .follow__icons span { width: 14px; height: 14px; border-radius: 50%; background: var(--red); }

  .appointment { position: absolute; left: 34px; top: 176px; width: 562px; color: var(--red); }
  .appointment__title { font-size: 20px; font-weight: 700; margin-bottom: 14px; }
  .field-row { display: flex; gap: 16px; }
  .field { display: flex; align-items: flex-end; font-size: 15px; margin-bottom: 16px; flex: 1; }
  .field__label { white-space: nowrap; margin-right: 6px; }
  .field__line { flex: 1; border-bottom: 1px dotted var(--dots); height: 1px; margin-bottom: 4px; }
  .field__suffix { font-size: 11px; font-weight: 700; margin-left: 4px; }

  .locations { position: absolute; left: 34px; top: 284px; font-size: 12px; line-height: 1.3; color: var(--ink); font-weight: 700; }
  .locations__title { color: var(--red); font-size: 13px; }

  /* Front: designer side */
  .front__rule { position: absolute; left: 40px; right: 40px; top: 84px; border-top: 1px solid var(--rule); }
  .front__brand { position: absolute; right: 40px; top: 128px; display: flex; align-items: center; gap: 10px;
    font-family: "Tinos", serif; font-size: 28px; font-weight: 700; color: var(--red); }
  .front__square { width: 24px; height: 24px; background: var(--red); }
  .designer { position: absolute; left: 40px; top: 176px; font-family: "Tinos", serif; }
  .designer__name { font-size: 24px; color: var(--red); letter-spacing: .5px; }
  .designer__title { font-size: 15px; color: var(--ink); letter-spacing: .5px; padding-bottom: 4px; border-bottom: 1px solid var(--ink); width: 240px; }
  .contact { position: absolute; left: 40px; bottom: 38px; list-style: none; font-family: "Tinos", serif; font-size: 15px; color: var(--grey); }
  .contact li { display: flex; align-items: center; gap: 10px; margin-top: 4px; }
  .contact svg { width: 13px; height: 13px; fill: var(--red); flex: none; }
</style>
</head>
<body>

<section class="card card--back" aria-label="Appointment card">
  <div class="brand">
    <div class="brand__name"><span class="brand__square"></span>Bright Lane Interiors</div>
    <div class="brand__tagline">Blinds, Shades, Shutters, Draperies &amp; Decor</div>
  </div>

  <div class="partner"><span class="partner__mark"></span>Marlow Fenwick</div>

  <div class="follow">FOLLOW US
    <div class="follow__icons"><span></span><span></span><span></span><span></span></div>
  </div>

  <div class="appointment">
    <div class="appointment__title">Appointment</div>
    <div class="field-row">
      <div class="field"><span class="field__label">Name :</span><span class="field__line"></span></div>
      <div class="field"><span class="field__label">Time :</span><span class="field__line"></span><span class="field__suffix">AM/PM</span></div>
    </div>
    <div class="field"><span class="field__label">Date :</span><span class="field__line"></span></div>
  </div>

  <div class="locations">
    <div class="locations__title">SHOWROOM LOCATIONS</div>
    <div>MAPLE RIDGE | CEDAR HILL</div>
    <div>WESTBROOK | NORTHGATE</div>
    <div>PINE HOLLOW</div>
  </div>
</section>

<section class="card card--front" aria-label="Designer card">
  <div class="front__rule"></div>
  <div class="front__brand"><span class="front__square"></span>Bright Lane Interiors</div>

  <div class="designer">
    <div class="designer__name">JORDAN AVERY</div>
    <div class="designer__title">DESIGNER</div>
  </div>

  <ul class="contact">
    <li><svg viewBox="0 0 24 24"><path d="M6.6 10.8a15 15 0 0 0 6.6 6.6l2.2-2.2a1 1 0 0 1 1-.25 11.4 11.4 0 0 0 3.6.6 1 1 0 0 1 1 1V20a1 1 0 0 1-1 1A17 17 0 0 1 3 4a1 1 0 0 1 1-1h3.5a1 1 0 0 1 1 1c0 1.25.2 2.45.6 3.6a1 1 0 0 1-.25 1z"/></svg>913.555.0147</li>
    <li><svg viewBox="0 0 24 24"><path d="M2 5h20v14H2z M2 5l10 8 10-8" fill="none" stroke="#c8383c" stroke-width="2.5"/></svg>info@brightlaneinteriors.com</li>
    <li><svg viewBox="0 0 24 24"><circle cx="12" cy="12" r="10"/></svg>brightlaneinteriors.com</li>
  </ul>
</section>

</body>
</html>
```